Luxury Wine Label for New Startup Winery

We need a wine label for our new winery startup. We have worked with a local designer but do not feel the resulting label / logo have the elevation required to present our brand as a luxury wine. Our winery is called "Quailbrook Vineyards" and we are focused on extremely high quality hand crafted artisan and estate wines from the Pacific Northwest.
We would like to see designs that utilize a tree line, or other imagery that represents the "Quailbrook" part of our company name. Another interesting feature could be wood grain.
A logo will be required based on your design so please design with this in mind:
This logo should be consistent with the wine bottle label design, and should be representative of our high end exclusive wine while giving a sense of place (Oregon/ Pacific Northwest.)
I will supply an image of the design we received from our local designer, PLEASE NOTE: in general we do like wood grain and tree line concepts but feel the execution was poorly done.
ATTN: Logo design should be suitable for use on: Bottles (Red wine/rose/white wine), Bussiness cards, vehicle signage, business signage, etc
P.S.:
If you have a design that is not outside the box we are still interested in seeing it.
Label is for a burgundy style bottle with a label height of 3.5 - 4" and a width of 3.5-4"
any label <= 4"x4" and >=3.5"x3.5" will be acceptable:
HOWEVER Width should be greater than or equal to height due to the bottle format
Target Market(s)
Wine enthusiasts with adequate discretionary budgets to afford $100 bottles of wine.
Industry/Entity Type
Wine / Winery
Requirements
Must have
- A sense of luxury, a feel of exclusivity, and a theme consistent with our product and brand name
Nice to have
- Tree line, wood grain or other wood themes. Serif fonts
Should not have
- anything cheesy, off topic, hard to read script fonts or anything that makes the label hard to read from a few feet away or too busy

```html
<!DOCTYPE html>
<html lang="en">
<head>
<meta charset="utf-8">
<title>Quailbrook Vineyards – Rose Label</title>
<link rel="stylesheet" href="https://fonts.googleapis.com/css2?family=Cormorant+Garamond:wght@500&family=Cinzel:wght@600&family=Allura&display=swap">
<style>
  :root {
    --stage: #16253a;
    --paper: #fbf9fa;
    --blush-light: #f1dbe9;
    --blush: #e3bcd6;
    --band-top: #f4dcec;
    --band-bottom: #d9a9c8;
    --ink: #1b1b1d;
    --gold: #b8954a;
    --gold-light: #d8bd7c;
  }
  * { box-sizing: border-box; margin: 0; padding: 0; }
  html, body {
    width: 1200px;
    height: 860px;
    overflow: hidden;
    background: var(--stage);
  }
  .canvas {
    position: relative;
    width: 1200px;
    height: 860px;
    display: flex;
    align-items: center;
    justify-content: center;
  }
  .label {
    position: relative;
    width: 780px;
    height: 680px;
    background: var(--paper);
    box-shadow: 0 20px 50px rgba(0, 0, 0, 0.35);
    overflow: hidden;
  }
  .label__pattern {
    position: absolute;
    inset: 0 0 240px 0;
    background:
      radial-gradient(ellipse 60% 45% at 20% 70%, var(--blush) 0%, transparent 70%),
      radial-gradient(ellipse 50% 40% at 85% 30%, var(--blush-light) 0%, transparent 70%),
      linear-gradient(160deg, var(--paper) 0%, var(--blush-light) 55%, var(--paper) 100%);
  }
  .label__frame {
    position: absolute;
    inset: 18px 18px 258px 18px;
    border: 1px solid rgba(27, 27, 29, 0.55);
  }
  .brand {
    position: absolute;
    left: 0;
    right: 0;
    top: 150px;
    display: flex;
    flex-direction: column;
    align-items: center;
    gap: 30px;
  }
  .brand__square {
    width: 110px;
    height: 110px;
    background: var(--ink);
  }
  .brand__name {
    font-family: "Cormorant Garamond", Georgia, serif;
    font-weight: 500;
    font-size: 44px;
    letter-spacing: 0.22em;
    color: var(--ink);
    text-transform: uppercase;
    white-space: nowrap;
  }
  .band {
    position: absolute;
    left: 0;
    right: 0;
    bottom: 0;
    height: 240px;
    background: linear-gradient(180deg, var(--band-top) 0%, var(--band-bottom) 100%);
    border-top: 3px solid var(--ink);
  }
  .band__outline {
    position: absolute;
    inset: 22px 26px;
    border: 2px solid var(--gold);
    border-radius: 60px;
  }
  .varietal {
    position: absolute;
    left: 0;
    right: 0;
    top: 46px;
    text-align: center;
    font-family: "Allura", cursive;
    font-size: 84px;
    line-height: 1;
    color: var(--ink);
  }
  .origin {
    position: absolute;
    left: 0;
    right: 0;
    top: 152px;
    display: flex;
    justify-content: center;
    align-items: center;
    gap: 22px;
    font-family: "Cinzel", Georgia, serif;
    font-weight: 600;
    font-size: 22px;
    letter-spacing: 0.14em;
  }
  .origin__region { color: var(--gold); }
  .origin__vintage {
    color: var(--ink);
    font-family: "Cormorant Garamond", Georgia, serif;
    font-size: 26px;
    letter-spacing: 0.1em;
  }
  .origin__divider {
    width: 1px;
    height: 28px;
    background: var(--ink);
  }
</style>
</head>
<body>
  <main class="canvas">
    <section class="label">
      <div class="label__pattern" role="img" aria-label="Soft pink topographic wood-grain pattern across the upper label"></div>
      <div class="label__frame"></div>

      <div class="brand">
        <div class="brand__square"></div>
        <h1 class="brand__name">Quailbrook Vineyards</h1>
      </div>

      <div class="band">
        <div class="band__outline"></div>
        <p class="varietal">Rose</p>
        <p class="origin">
          <span class="origin__region">Pacific</span>
          <span class="origin__divider"></span>
          <span class="origin__vintage">2025</span>
          <span class="origin__divider"></span>
          <span class="origin__region">Northwest</span>
        </p>
      </div>
    </section>
  </main>
</body>
</html>
```